Advertising company unique advertising platform

we need a logo design for a new company based in Australia Melbourne. We develop innovated advertising platform where consumer can use this platform to get regular discount, as business owner they can use this platform for free advertisement. Payment for this advertisement platform only payable every two weeks, when I generate revenue for their business

Industry/Entity Type

Advertising

Contact Information for Business Card

Dale Morven | Co-Founder |Managing Director
Suite 718 240 Wattlebrook Lane Melbourne Vic 3000

ABN 38 614 207 923
Tel: +61 0487 259 318 | Email: dale.morven@plivorantu.com

Font styles to use
Decorative
Script

Requirements
Must have
• Try few different design and some round corner business card
Should not have
• One round corner business card...try 4 different colour background not only black, make sure two side is designed. Be creative so imagine you are giving this to a client make sure has wow factor, if you can also try one design with engrave like all the logo, words look 3d feel
• The word Advertising Platform use attached file font

```html
<!DOCTYPE html>
<html lang="en">
<head>
<meta charset="utf-8">
<title>Lumora Reach – Business Card</title>
<link href="https://fonts.googleapis.com/css2?family=Roboto:wght@400;500;700&display=swap" rel="stylesheet">
<style>
  :root {
    --stage: #e9e6e2;
    --flame-yellow: #f6cf45;
    --flame-orange: #ef8a32;
    --flame-red: #e2452b;
    --card-dark: #262626;
    --ink-dark: #1f1a17;
    --ink-light: #f2f2f2;
    --accent-red: #ee4a2a;
    --accent-teal: #2fe0b3;
    --bar-top: #f2a33c;
    --bar-bottom: #e8552b;
  }
  * { box-sizing: border-box; margin: 0; padding: 0; }
  html, body { width: 1200px; height: 886px; overflow: hidden; }
  body {
    background: var(--stage);
    font-family: "Roboto", Arial, sans-serif;
    position: relative;
  }
  .card {
    position: absolute;
    width: 580px;
    height: 332px;
    border-radius: 24px;
    overflow: hidden;
    box-shadow: 0 10px 28px rgba(0,0,0,0.22);
  }
  /* Front side */
  .card--front {
    left: 70px; top: 80px;
    background: radial-gradient(ellipse 70% 80% at 42% 42%, var(--flame-yellow) 0%, var(--flame-orange) 55%, var(--flame-red) 100%);
  }
  .front__brand {
    position: absolute;
    left: 0; right: 0; top: 118px;
    display: flex; align-items: center; justify-content: center; gap: 16px;
  }
  .front__dot {
    width: 46px; height: 46px; border-radius: 50%;
    background: var(--ink-dark);
  }
  .front__name {
    font-size: 46px; font-weight: 700;
    color: var(--ink-dark);
    letter-spacing: 1px;
  }
  .front__web {
    position: absolute; left: 0; right: 0; top: 250px;
    text-align: center;
    font-size: 14px; letter-spacing: 6px;
    color: var(--ink-dark);
  }
  /* Back side */
  .card--back {
    left: 550px; top: 474px;
    background: linear-gradient(160deg, #2e2e2e 0%, var(--card-dark) 60%, #1e1e1e 100%);
  }
  .back__bar {
    position: absolute; left: 64px; top: 118px;
    width: 34px; height: 214px;
    background: linear-gradient(180deg, var(--bar-top), var(--bar-bottom));
  }
  .back__bar svg { display: block; }
  .back__brand {
    position: absolute; left: 58px; top: 58px;
    display: flex; align-items: center; gap: 10px;
  }
  .back__dot {
    width: 46px; height: 46px; border-radius: 50%;
    background: var(--flame-orange);
  }
  .back__name {
    font-size: 30px; font-weight: 700;
    color: var(--accent-teal);
  }
  .back__details {
    position: absolute; left: 118px; top: 142px;
    color: var(--ink-light);
    font-size: 15px; line-height: 20px;
  }
  .back__details .gap { margin-top: 8px; }
  .back__person {
    position: absolute; right: 40px; top: 140px;
    text-align: right; text-transform: uppercase;
  }
  .person__name {
    color: var(--accent-red);
    font-size: 22px; font-weight: 500;
  }
  .person__role {
    color: var(--accent-teal);
    font-size: 16px; font-weight: 500; line-height: 19px;
  }
</style>
</head>
<body>
  <section class="card card--front" aria-label="Card front">
    <div class="front__brand">
      <span class="front__dot"></span>
      <span class="front__name">Lumora Reach</span>
    </div>
    <p class="front__web">www.plivorantu.com</p>
  </section>

  <section class="card card--back" aria-label="Card back">
    <div class="back__brand">
      <span class="back__dot"></span>
      <span class="back__name">Lumora Reach</span>
    </div>
    <div class="back__bar">
      <svg width="34" height="214" viewBox="0 0 34 214" fill="none" stroke="#2a2a2a" stroke-width="2">
        <!-- pin -->
        <path d="M17 14c-4 0-7 3-7 7 0 5 7 12 7 12s7-7 7-12c0-4-3-7-7-7z"/><circle cx="17" cy="21" r="2.2"/>
        <!-- pin -->
        <path d="M17 52c-4 0-7 3-7 7 0 5 7 12 7 12s7-7 7-12c0-4-3-7-7-7z"/><circle cx="17" cy="59" r="2.2"/>
        <!-- phone -->
        <path d="M11 94c2-2 4 0 5 2l-2 2c1 3 3 5 6 6l2-2c2 1 4 3 2 5-2 3-6 2-10-2s-6-8-3-11z" fill="#2a2a2a"/>
        <!-- mail -->
        <rect x="9" y="128" width="16" height="11" rx="1"/><path d="M9 129l8 6 8-6"/>
      </svg>
    </div>
    <div class="back__details">
      <p>Plivorantu</p>
      <p>ABN 38 614 207 923</p>
      <p class="gap">Suite 718 240 Wattlebrook Lane</p>
      <p>Melbourne Vic 3000</p>
      <p class="gap">+61 0487 259 318</p>
      <p>dale.morven@plivorantu.com</p>
    </div>
    <div class="back__person">
      <p class="person__name">Dale Morven</p>
      <p class="person__role">Co-Founder</p>
      <p class="person__role">Managing Director</p>
    </div>
  </section>
</body>
</html>
```